Business card design needed

Family General Practitioner/ Family Physician.
Logo is the logo of the Noble Guild of Family Healers Oceania
http://kpltw.varendo.example/ImageShelf/marks/pages/NGFHO%20mark_jpg.htm
Updates

Project Deadline Extended
Reason: Just a bit more time to make changes and the weekend for me to look at things closely and to choose. Thanks, Orin

Thanks for all the submissions. So many of them are really works of art. Not one of them are not good. The ones that I am eliminating are the ones that I think are not suitable for me personally only, and because if I don't, it makes it very difficult to decide as many of you are also sending me slight variations of a card. I have just decided to choose a second place card too. Can't thank you all enough. Good luck, Orin. P.S - Working today till 10 pm as the card says :-), so probably won't be able to give a feedback till late Saturday night or Sunday morning here in Sydney, Australia. 

Project Deadline Extended
Reason: Just added a second place to the budget and realised that Australia is ahead of the rest of the world in the time zone (only :-) - don't want to offend anyone or start a debate!! ) , so Monday deadline will mean it will be a weekend for the rest of the world. Just wanted to give everyone more time to submit their best, especially since I will be picking a second card too. Can't thank everyone enough for the submissions. P.S - Not keen on photos on the card.

Industry/Entity Type

Business

Contact Information for Business Card

Dr. Orin Halvey M.B.B.S., F.N.G.F.H.O
Family General Practitioner
Address, timings, phone and fax number on the back.

Requirements
Must have
• Timings
Mon 7 am - 7 pm
Tues 7 am - 12 pm
Wed 7 am - 10 pm
Thurs 7 am - 12 pm
Fri 7 am - 8 pm
Sat 8 am - 10 pm
Sun - Off

```html
<!DOCTYPE html>
<html lang="en">
<head>
<meta charset="utf-8">
<title>Dr. Orin Halvey – Business Card</title>
<link rel="stylesheet" href="https://fonts.googleapis.com/css2?family=Libre+Baskerville:wght@400;700&family=Marcellus+SC&family=PT+Sans:wght@400&display=swap">
<style>
  :root {
    --navy: #154157;
    --white: #ffffff;
    --backdrop: #ece4d6;
    --serif: "Libre Baskerville", Georgia, serif;
    --caps: "Marcellus SC", Georgia, serif;
    --sans: "PT Sans", Arial, sans-serif;
  }
  * { margin: 0; padding: 0; box-sizing: border-box; }
  html, body { width: 1200px; height: 417px; overflow: hidden; }
  body { background: var(--backdrop); position: relative; }

  .card { position: absolute; top: 58px; width: 532px; height: 304px; }

  /* Front */
  .card-front { left: 58px; background: var(--white); }
  .doctor-name {
    position: absolute; left: 26px; top: 62px;
    font-family: var(--serif); font-weight: 700; font-size: 31px;
    color: var(--navy); letter-spacing: 0.2px; white-space: nowrap;
  }
  .credentials {
    position: absolute; left: 102px; top: 112px;
    font-family: var(--serif); font-weight: 700; font-size: 10.5px;
    color: var(--navy); letter-spacing: 0.8px;
  }
  .specialty {
    position: absolute; left: 49px; top: 171px;
    font-family: var(--serif); font-weight: 700; font-size: 16px;
    color: var(--navy);
  }
  .guild-mark {
    position: absolute; left: 392px; top: 70px; width: 118px;
    display: flex; flex-direction: column; align-items: center; gap: 6px;
    text-align: center;
  }
  .guild-mark .dot { width: 34px; height: 34px; border-radius: 50%; background: var(--navy); }
  .guild-mark .guild-name {
    font-family: var(--serif); font-weight: 700; font-size: 10px;
    line-height: 1.3; color: var(--navy);
  }
  .rule { position: absolute; left: 0; width: 100%; height: 2px; background: var(--navy); }
  .rule-one { top: 252px; }
  .rule-two { top: 257px; }
  .base-band { position: absolute; left: 0; bottom: 0; width: 100%; height: 34px; background: var(--navy); }

  /* Back */
  .card-back { left: 619px; background: var(--navy); color: var(--white); }
  .hours-title {
    position: absolute; left: 56px; top: 79px;
    font-family: var(--serif); font-size: 15px;
  }
  .hours-table {
    position: absolute; left: 32px; top: 109px;
    border-collapse: collapse;
  }
  .hours-table td { height: 16.6px; padding: 0; vertical-align: middle; }
  .hours-table .day { font-family: var(--serif); font-weight: 700; font-size: 12.5px; width: 82px; }
  .hours-table .sep { font-family: var(--sans); font-size: 12px; width: 20px; }
  .hours-table .time { font-family: var(--sans); font-size: 12px; white-space: pre; }
  .divider { position: absolute; left: 243px; top: 73px; width: 2px; height: 158px; background: var(--white); }
  .address {
    position: absolute; left: 270px; top: 124px;
    font-family: var(--caps); font-size: 12px; line-height: 20px;
    letter-spacing: 0.8px; font-style: normal;
  }
</style>
</head>
<body>
  <section class="card card-front">
    <h1 class="doctor-name">Dr. Orin Halvey</h1>
    <p class="credentials">M.B.B.S., F.N.G.F.H.O</p>
    <p class="specialty">Family General Practitioner</p>
    <div class="guild-mark">
      <span class="dot"></span>
      <span class="guild-name">Noble Guild of Family Healers Oceania</span>
    </div>
    <div class="rule rule-one"></div>
    <div class="rule rule-two"></div>
    <div class="base-band"></div>
  </section>

  <section class="card card-back">
    <h2 class="hours-title">Working Hours</h2>
    <table class="hours-table">
      <tr><td class="day">Monday</td><td class="sep">:</td><td class="time">7 AM -  7 PM</td></tr>
      <tr><td class="day">Tuesday</td><td class="sep">:</td><td class="time">7 AM - 12 PM</td></tr>
      <tr><td class="day">Wednesday</td><td class="sep">:</td><td class="time">7 AM - 10 PM</td></tr>
      <tr><td class="day">Thursday</td><td class="sep">:</td><td class="time">7 AM - 12 PM</td></tr>
      <tr><td class="day">Friday</td><td class="sep">:</td><td class="time">7 AM -  8 PM</td></tr>
      <tr><td class="day">Saturday</td><td class="sep">:</td><td class="time">8 AM - 10 PM</td></tr>
      <tr><td class="day">Sunday</td><td class="sep">:</td><td class="time">OFF</td></tr>
    </table>
    <div class="divider"></div>
    <address class="address">
      Upper Level, Harbour Court,<br>
      Ferngate Shopping Center<br>
      Ferngate, NSW 2199
    </address>
  </section>
</body>
</html>
```